Website for my photography business

I need a website for my photography business, Bram Kellet Photography. I need a website that has a landing page with a cover photo of each kind of photography I do. For example, Nature, Weddings, Portraits and Architecture. I want it so that when someone comes onto my website they have to choose which kind of photography page they want to visit. So if they click on the wedding photo it will open to a page with my wedding portfolio images and a contact me button. If they choose nature photography I want them to be redirected to an e-commerce section where they can purchase prints. Architecture and Portraits should open up to their respective portfolios with about me and contact info. I like this kind of format because I want people who come to my website for a specific type of photography to be able to be directed there easily without having to look at a mix of other kinds of photography. I will provide a few files to use as placeholders. I have already purchased the bramkelletphotography.example domain name. A Wix website would be great because I am most familiar with it but I am open to anything.

Industry/Entity Type

Photographer

Number of Pages Required

5+ page

Requirements
Must have
• Landing Page and e-commerce

```html
<!DOCTYPE html>
<html lang="en">
<head>
<meta charset="utf-8">
<title>Bram Kellet Photography</title>
<link href="https://fonts.googleapis.com/css2?family=Poppins:wght@300;400;600&display=swap" rel="stylesheet">
<style>
  :root {
    --bg: #050b12;
    --bg-soft: #0c141d;
    --ink: #ffffff;
    --ink-muted: #d9dde2;
    --logo: #3a4766;
    --navy: #13223a;
    --green: #4aa523;
    --orange: #ee8a2e;
    --brown: #8a6a4a;
  }
  * { box-sizing: border-box; margin: 0; padding: 0; }
  html, body { width: 1200px; height: 800px; overflow: hidden; }
  body {
    position: relative;
    background: radial-gradient(ellipse at 50% 40%, var(--bg-soft) 0%, var(--bg) 70%);
    font-family: "Poppins", sans-serif;
    color: var(--ink);
  }
  .brand { position: absolute; left: 108px; top: 40px; color: var(--logo); }
  .brand-name { font-size: 34px; font-weight: 400; letter-spacing: 0.5px; line-height: 1; white-space: nowrap; }
  .brand-tagline { font-size: 8px; font-weight: 400; margin: 10px 0 0 170px; white-space: nowrap; }
  .main-nav { position: absolute; top: 62px; left: 0; width: 1200px; }
  .main-nav a {
    position: absolute; transform: translateX(-50%);
    color: var(--ink-muted); text-decoration: none;
    font-size: 16px; font-weight: 300; letter-spacing: 1px;
  }
  .category { position: absolute; display: block; }
  .category-photo { position: absolute; display: block; }
  .category-label {
    position: absolute; display: flex; align-items: center; justify-content: center;
    font-size: 35px; font-weight: 600; color: var(--ink); white-space: nowrap;
  }
  .weddings .category-photo { left: 108px; top: 185px; width: 238px; height: 443px;
    background: linear-gradient(160deg, #a08a78 0%, #5e534e 35%, #1c2638 55%, #8c7a6a 80%, #b49c86 100%); }
  .weddings .category-label { left: 250px; top: 185px; width: 230px; height: 66px; background: var(--navy); }
  .portraits .category-photo { left: 357px; top: 265px; width: 238px; height: 443px;
    background: linear-gradient(180deg, #ccd4dc 0%, #2b3a2c 30%, #b8632a 55%, #c77a3c 70%, #f4f6f8 90%); }
  .portraits .category-label { left: 506px; top: 642px; width: 218px; height: 66px; background: var(--orange); }
  .nature .category-photo { left: 605px; top: 199px; width: 238px; height: 411px;
    background: linear-gradient(170deg, #9a9a9a 0%, #5a5a5a 35%, #b6b6b6 60%, #4c4c4c 100%); }
  .nature .category-label { left: 654px; top: 372px; width: 189px; height: 66px; background: var(--green); }
  .architecture .category-photo { left: 854px; top: 185px; width: 238px; height: 443px;
    background: linear-gradient(180deg, #d8dde2 0%, #9a5a44 25%, #b98f72 55%, #8a5540 75%, #b5aca2 100%); }
  .architecture .category-label { left: 815px; top: 629px; width: 277px; height: 65px; background: var(--brown); }
  .site-footer { position: absolute; left: 0; top: 764px; width: 1200px; font-size: 13px; }
  .footer-email { position: absolute; left: 106px; font-weight: 300; }
  .social { position: absolute; left: 596px; transform: translateX(-50%); display: flex; gap: 10px; font-size: 11px; font-weight: 400; }
  .social a { color: var(--ink); text-decoration: none; }
  .copyright { position: absolute; right: 110px; font-size: 11px; font-weight: 300; top: 2px; }
</style>
</head>
<body>
  <header>
    <div class="brand">
      <div class="brand-name">Bram Kellet Photography</div>
      <div class="brand-tagline">Creating extraordinary images that last infinitely</div>
    </div>
    <nav class="main-nav">
      <a href="#" style="left:650px">Home</a>
      <a href="#" style="left:774px">Bio</a>
      <a href="#" style="left:903px">Clients</a>
      <a href="#" style="left:1055px">Portfolio</a>
    </nav>
  </header>

  <main>
    <a class="category weddings" href="#">
      <span class="category-photo" role="img" aria-label="Wedding rings resting on a granite rock"></span>
      <span class="category-label">Weddings</span>
    </a>
    <a class="category portraits" href="#">
      <span class="category-photo" role="img" aria-label="Red fox sitting in snow among pine trees"></span>
      <span class="category-label">Portraits</span>
    </a>
    <a class="category nature" href="#">
      <span class="category-photo" role="img" aria-label="Black and white abstract study of soft curves"></span>
      <span class="category-label">Nature</span>
    </a>
    <a class="category architecture" href="#">
      <span class="category-photo" role="img" aria-label="Brick and stone building with a police car parked in front"></span>
      <span class="category-label">Architecture</span>
    </a>
  </main>

  <footer class="site-footer">
    <span class="footer-email">info@bramkelletphotography.example</span>
    <span class="social">
      <a href="#">Snapline</a>
      <a href="#">Pixfeed</a>
      <a href="#">Chirper</a>
    </span>
    <span class="copyright">© Copyright 2020 The Company name. All Rights Reserved.</span>
  </footer>
</body>
</html>
```